Restyle corporate identity (+ logo) for a road construction company

We need a new logo and stationary design for our company VARNOK path. VARNOK path® increases the road base strength, while reducing major costs and time of road construction. Attached some examples of the current design.

Our wishes for the new logo:
- Business look
- Style sheet
- Modern

More information: www.varnokpath.example
Updates

Target Market(s)

Government

Industry/Entity Type

Construction

Requirements
Must have
• Logo (with road sign) + text

```html
<!DOCTYPE html>
<html lang="en">
<head>
<meta charset="utf-8">
<title>VARNOK path — business card</title>
<link rel="stylesheet" href="https://fonts.googleapis.com/css2?family=Source+Sans+3:wght@400;600&display=swap">
<style>
  :root {
    --backdrop: #9b9b9b;
    --card-white: #ebebed;
    --brand-blue: #0a78e0;
    --brand-blue-bright: #1a86e6;
    --ink: #4a4a4f;
    --ink-soft: #8a8a90;
    --rule: #c4c4c8;
    --strip-grey: #a9a9ad;
    --white: #ffffff;
  }
  * { box-sizing: border-box; margin: 0; padding: 0; }
  html, body {
    width: 1105px; height: 1200px; overflow: hidden;
    background: var(--backdrop);
    font-family: "Source Sans 3", sans-serif;
  }
  .card {
    position: absolute; left: 182px; width: 746px; height: 427px; overflow: hidden;
  }
  .card--front { top: 119px; background: var(--card-white); }
  .card--back { top: 637px; background: var(--brand-blue); }

  /* front */
  .brand {
    position: absolute; left: 80px; top: 150px;
    display: flex; align-items: center; gap: 14px;
    color: var(--brand-blue); font-weight: 600;
  }
  .brand__square { width: 60px; height: 60px; background: var(--brand-blue); border-radius: 4px; }
  .brand__name { line-height: 1; }
  .brand__line1 { display: block; font-size: 52px; letter-spacing: 1px; }
  .brand__line2 { display: block; font-size: 40px; letter-spacing: 17px; margin-top: 4px; }

  .divider {
    position: absolute; left: 395px; top: 81px; width: 1px; height: 239px; background: var(--rule);
  }
  .contact { position: absolute; left: 427px; top: 88px; color: var(--ink); }
  .contact__name {
    font-size: 26px; font-weight: 600; color: var(--brand-blue); letter-spacing: .5px; line-height: 1.1;
  }
  .contact__role { font-size: 19px; color: var(--ink-soft); line-height: 1.2; }
  .contact__address { margin-top: 20px; font-size: 19.5px; line-height: 27px; }
  .contact__lines { margin-top: 12px; font-size: 19.5px; line-height: 29px; list-style: none; }
  .contact__lines li { display: flex; align-items: center; gap: 10px; }
  .contact__lines svg { width: 16px; height: 16px; fill: var(--brand-blue); flex: none; }

  .footer-band { position: absolute; left: 0; bottom: 0; width: 746px; height: 46px; }
  .footer-url {
    position: absolute; left: 457px; bottom: 11px;
    color: var(--white); font-size: 19px; letter-spacing: 3px;
  }

  /* back */
  .back-brand {
    position: absolute; right: 56px; top: 232px; text-align: right;
    color: var(--white); font-weight: 600; line-height: 1;
  }
  .back-brand__line1 { display: block; font-size: 76px; letter-spacing: 1px; }
  .back-brand__line2 { display: block; font-size: 56px; letter-spacing: 22px; margin-right: -22px; margin-top: 4px; }
  .back-url {
    position: absolute; right: 56px; top: 360px;
    color: var(--white); font-size: 20px; letter-spacing: 1.5px;
  }
</style>
</head>
<body>
  <section class="card card--front" aria-label="Business card front">
    <div class="brand">
      <span class="brand__square"></span>
      <span class="brand__name">
        <span class="brand__line1">VARNOK</span>
        <span class="brand__line2">PATH</span>
      </span>
    </div>

    <div class="divider"></div>

    <div class="contact">
      <p class="contact__name">MAREN VOSTEL</p>
      <p class="contact__role">CEO/Founder</p>
      <p class="contact__address">Lindqvist Kade 27<br>4812 ZT Veldhaven<br>The Netherlands</p>
      <ul class="contact__lines">
        <li>
          <svg viewBox="0 0 24 24" aria-hidden="true"><path d="M6.6 10.8a15.1 15.1 0 0 0 6.6 6.6l2.2-2.2c.3-.3.7-.4 1-.2 1.1.4 2.3.6 3.6.6.6 0 1 .4 1 1V20c0 .6-.4 1-1 1A17 17 0 0 1 3 4c0-.6.4-1 1-1h3.5c.6 0 1 .4 1 1 0 1.3.2 2.5.6 3.6.1.3 0 .7-.2 1z"/></svg>
          555 210 4837
        </li>
        <li>
          <svg viewBox="0 0 24 24" aria-hidden="true"><path d="M2 5h20v14H2z M2 5l10 8 10-8" fill="var(--brand-blue)"/><path d="M2 6l10 7.5L22 6" fill="none" stroke="var(--card-white)" stroke-width="1.6"/></svg>
          hello@varnokpath.example
        </li>
      </ul>
    </div>

    <svg class="footer-band" viewBox="0 0 746 46" aria-hidden="true">
      <polygon points="0,33 440,33 395,46 0,46" fill="var(--strip-grey)"/>
      <polygon points="436,0 746,0 746,46 395,46" fill="var(--brand-blue)"/>
    </svg>
    <p class="footer-url">www.varnokpath.example</p>
  </section>

  <section class="card card--back" aria-label="Business card back">
    <div class="back-brand">
      <span class="back-brand__line1">VARNOK</span>
      <span class="back-brand__line2">PATH</span>
    </div>
    <p class="back-url">www.varnokpath.example</p>
  </section>
</body>
</html>
```